Design a Website in Wordpress for an Australian Health Training Company in Health related courses

We require a WORDPRESS based Website (due to add on's we need to use for third party software) to replace our old site.
We offer national face to face delivery in medical reception, terminology and also administration.
The website will have around 6 pages and the ability to describe our main 6 courses (perhaps on the Courses page this may be tabs opening up to details for example?)
I have attached a previous sample of a Joomla site which was being developed (please do not feel you have to copy this - but I am just giving it as a sample - copying would be boring). But it gives an idea of look/feel and colours which may be suitable. Open to other ideas though.
I will provide some of the content, but would like the ability to finish the content myself.
Images and graphics are important. While a few medical photos re great - don't be tempted to us all pictures of doctors and nurses (although a couple would be good) - these are administrative courses so general corporate, eye catching visionary pictures of people in general are great. A medical type picture is also fine.
THE BOOKING system - will be via an ADD ON which will occur at the end of the project and is supplied by a third party software company (our student management system). This project will include up to 2 hours working with the Tech guys from the third party software to enable the ADD ON. If this ADD ON requires more time, we will pay hourly (although I do not expect it will).
Target Market(s)
Mostly a female market, many mature aged women target 25-45 yrs. Mixture of medical/health and corporate. Maybe a bit of mums returning to work and corporate inspiration.
Industry/Entity Type
It Company
Coding
Coded - Design and coding required
Number of Pages Required
5+ page
Requirements
Must have
- Wordpress
- Great graphics
- Interesting
- professional and clean
- Enquiry section (info Pak)
- Should have a University feel to it - Education
- Pages
- Home Page - About Us - Recruitment -Courses - Class Schedule - Traineeships Queensland Funding - Latest News Blog - Corporate Training- Contact us

```html
<!DOCTYPE html>
<html lang="en">
<head>
<meta charset="utf-8">
<title>Harwood Institute of Training</title>
<link rel="stylesheet" href="https://fonts.googleapis.com/css2?family=Raleway:wght@400;500;600;700&family=Open+Sans:wght@400;600;700&display=swap">
<style>
:root{
  --orange:#f7941d;
  --navy:#2a3a5e;
  --navy-deep:#23304f;
  --footer:#1f2b47;
  --copy:#1a243c;
  --nav:#3b3b3b;
  --ink:#333;
  --muted:#666;
  --peach:#fdf1ea;
  --grey-band:#dcdcdc;
  --line:#e2e2e2;
  --white:#fff;
}
*{box-sizing:border-box;margin:0;padding:0}
html,body{width:1200px;height:4157px;overflow:hidden}
body{font-family:"Open Sans",Arial,sans-serif;color:var(--ink);background:var(--white);font-size:14px}
h1,h2,h3,h4{font-family:"Raleway",Arial,sans-serif}
.wrap{width:1100px;margin:0 auto;position:relative}
.btn{display:inline-block;background:var(--orange);color:#fff;font-family:"Raleway",sans-serif;font-weight:700;font-size:13px;text-transform:uppercase;padding:12px 28px;letter-spacing:.5px}
.section-title{font-family:"Raleway",sans-serif;font-weight:400;font-size:34px;text-transform:uppercase;text-align:center;color:#333;letter-spacing:.5px}

/* top bar */
.topbar{height:50px;border-bottom:1px solid var(--line);font-size:13px;color:#555}
.topbar .wrap{display:flex;align-items:center;height:50px}
.topbar .contact{display:flex;gap:26px;align-items:center}
.topbar .contact span{display:flex;gap:8px;align-items:center}
.topbar .right{margin-left:auto;display:flex;align-items:center;gap:24px}
.social{display:flex;gap:6px}
.social i{display:block;width:26px;height:26px;border-radius:50%;background:#9a9a9a}
.topbar .links{display:flex;gap:16px}

/* header */
.header{height:122px}
.header .wrap{display:flex;align-items:center;height:122px}
.brand{display:flex;align-items:center;gap:12px}
.brand .mark{width:40px;height:40px;background:var(--navy)}
.brand .name{font-family:"Raleway",sans-serif;font-weight:700;font-size:15px;color:var(--navy);line-height:1.25;text-transform:uppercase;width:150px}
.header .actions{margin-left:auto;display:flex;gap:14px;align-items:center}
.header .actions .btn{padding:14px 34px;font-size:14px}
.header .actions .btn.navy{background:var(--navy)}
.search-btn{width:48px;height:44px;background:#eee;display:flex;align-items:center;justify-content:center}

/* nav */
.mainnav{height:50px;background:var(--nav)}
.mainnav ul{list-style:none;display:flex;justify-content:space-between;width:1100px;margin:0 auto;height:50px;align-items:center}
.mainnav a{color:#fff;font-family:"Raleway",sans-serif;font-weight:700;font-size:12.5px;text-transform:uppercase;text-decoration:none}

/* hero */
.hero{height:518px;position:relative;background:linear-gradient(180deg,#3d3a44 0%,#5c4a3e 45%,#8a5a2e 70%,#2a2830 100%);text-align:center;color:#fff}
.hero .copy{position:absolute;top:170px;left:0;right:0}
.hero h1{font-weight:700;font-size:38px;text-transform:uppercase;letter-spacing:1px}
.hero p{font-family:"Raleway",sans-serif;font-weight:600;font-size:23px;line-height:1.45;margin:16px auto 22px;width:760px}
.dots{position:absolute;bottom:38px;left:0;right:0;display:flex;justify-content:center;gap:8px}
.dots i{width:10px;height:10px;border-radius:50%;background:#fff;opacity:.6}
.dots i:first-child{opacity:1;background:transparent;border:2px solid #fff}

/* welcome */
.welcome{height:318px;text-align:center;padding-top:52px}
.welcome p{font-size:14px;color:var(--muted);line-height:1.95;width:1100px;margin:22px auto 30px}

/* courses */
.courses{height:488px;background:var(--peach);padding-top:38px}
.course-row{display:flex;justify-content:space-between;margin-top:38px;padding:0 40px}
.course{width:230px;text-align:center}
.course .icon{width:108px;height:108px;border-radius:50%;background:#fff;margin:0 auto;display:flex;align-items:center;justify-content:center;box-shadow:0 4px 0 var(--orange)}
.course h3{font-size:15px;font-weight:700;text-transform:uppercase;margin:38px 0 6px;line-height:1.4;color:#222}
.course p{font-size:14px;color:var(--muted);line-height:1.5}
.course .btn{margin-top:18px;padding:11px 34px}
.arrow{position:absolute;top:130px;color:#888;font-size:34px;line-height:1}
.arrow.l{left:-30px}.arrow.r{right:-30px}

/* traineeships */
.trainee{height:305px;background:var(--navy);color:#fff;text-align:center;padding-top:40px}
.trainee h2{font-weight:400;font-size:33px;text-transform:uppercase}
.trainee p{font-size:12.5px;line-height:2.1;width:1100px;margin:26px auto 18px;color:#dfe4ee}
.trainee .more{font-size:15px}

/* blog */
.blog{height:629px;padding-top:40px;position:relative}
.blog .dateline{position:absolute;top:138px;left:0;right:0;border-top:1px solid var(--line)}
.post-row{display:flex;justify-content:space-between;margin-top:36px;position:relative}
.post{width:328px}
.date{width:160px;height:48px;background:var(--peach);margin:0 auto 12px;display:flex;align-items:center;justify-content:center;gap:8px;font-size:14px}
.date b{color:var(--orange);font-size:26px;font-family:"Raleway",sans-serif}
.post .card{border:1px solid var(--line);background:#fff}
.post .photo{height:200px;margin:4px}
.post .body{padding:14px 14px 12px}
.post h3{font-size:15px;font-weight:700;text-transform:uppercase;color:#222}
.post p{font-size:13.5px;color:var(--muted);line-height:1.5;margin-top:8px}
.post .meta{display:flex;justify-content:space-between;border-top:1px solid var(--line);margin-top:18px;padding:10px 14px;font-size:12px}
.post .meta .rm{color:var(--orange);font-weight:700;text-transform:uppercase}
.blog .arrow{top:340px}

/* testimonials */
.testi{height:346px;background:var(--grey-band);padding-top:46px;position:relative}
.testi .arrow{top:150px;color:#999}
.testi .arrow.l{left:70px}.testi .arrow.r{left:auto;right:70px}
.quote-box{width:1000px;height:152px;margin:30px auto 0;background:#fff;padding:20px 40px;position:relative}
.quote-box p{font-style:italic;font-size:15px;color:#666;line-height:1.75}
.quote-box .q{position:absolute;font-family:Georgia,serif;font-size:90px;color:#ddd;line-height:1}
.quote-box .q.open{left:12px;top:4px}.quote-box .q.close{right:20px;bottom:-34px}
.author{position:absolute;left:50%;transform:translateX(-50%);bottom:-36px;width:210px;height:86px;background:var(--orange);color:#fff;text-align:center;padding-top:22px;z-index:2}
.author b{font-family:"Raleway",sans-serif;font-size:15px;text-transform:uppercase;display:block}
.author span{font-size:14px}

/* why + form */
.split{height:657px;display:flex}
.why{width:600px;background:var(--navy);color:#fff;padding:78px 0 0 75px}
.why h2,.infopack h2{font-weight:400;font-size:33px;text-transform:uppercase}
.why dl{margin-top:28px;width:430px}
.why dt{color:var(--orange);font-weight:700;font-size:14px;text-transform:uppercase;margin-top:18px}
.why dd{font-size:14px;line-height:1.6;margin-top:8px;color:#e3e7ef}
.infopack{width:600px;background:var(--navy-deep);color:#fff;padding:78px 75px 0 38px}
.form{margin-top:30px;display:flex;flex-direction:column;gap:13px}
.field{height:48px;background:#fff;color:#555;font-size:14px;padding:14px 16px}
.field.msg{height:146px}
.send{align-self:flex-end;width:332px;height:42px;background:var(--orange);color:#fff;font-weight:700;text-align:center;line-height:42px;font-size:14px}

/* cta */
.cta{height:249px;text-align:center;padding-top:50px}
.cta p{font-family:"Raleway",sans-serif;font-size:31px;color:var(--navy);line-height:1.3}
.cta .btn{margin-top:32px;width:330px;padding:14px 0}

/* footer */
.footer{height:355px;background:var(--footer);color:#cfd5e2;padding-top:44px}
.footer .wrap{display:flex;justify-content:space-between}
.fcol{width:240px;font-size:13px;line-height:1.55}
.fcol h4{font-size:15px;font-weight:600;color:#fff;text-transform:uppercase;margin-bottom:18px}
.fcol .item{margin-bottom:18px}
.fcol .item em{display:block;color:var(--orange);font-style:normal;font-weight:600}
.fcol.about{width:250px}
.fcol.about .brand .name{color:#fff}
.fcol.about p{margin-top:32px}
.fsocial{display:flex;gap:6px;margin-top:20px}
.fsocial i{width:30px;height:30px;border-radius:50%;background:#fff}
.contact-list div{display:flex;gap:10px;align-items:center;margin-bottom:8px}
.contact-list .co{color:var(--orange);font-weight:700}
.news-in{height:34px;background:#fff;color:#777;font-size:12px;padding:9px 10px;margin-top:4px}
.news-go{display:flex;justify-content:flex-end;margin-top:10px}
.news-go span{background:var(--orange);color:#fff;font-weight:700;font-size:12px;padding:8px 12px}
.copyright{height:70px;background:var(--copy);color:#8b93a8;font-size:12px;text-align:center;line-height:70px}
</style>
</head>
<body>

<div class="topbar">
  <div class="wrap">
    <div class="contact">
      <span><svg width="14" height="14" viewBox="0 0 24 24"><path fill="#555" d="M6.6 10.8a15 15 0 006.6 6.6l2.2-2.2c.3-.3.7-.4 1-.2 1.1.4 2.3.6 3.6.6.6 0 1 .4 1 1V20c0 .6-.4 1-1 1A17 17 0 013 4c0-.6.4-1 1-1h3.5c.6 0 1 .4 1 1 0 1.3.2 2.5.6 3.6.1.3 0 .7-.2 1z"/></svg>1-800-555-0142</span>
      <span><svg width="14" height="12" viewBox="0 0 24 18"><rect width="24" height="18" fill="#555"/><path d="M0 0l12 9L24 0" stroke="#fff" stroke-width="2" fill="none"/></svg>info@harwoodinstitute.example</span>
    </div>
    <div class="right">
      <div class="social"><i></i><i></i><i></i><i></i><i></i></div>
      <div class="links"><span>Log in</span><span>|</span><span>Register</span></div>
    </div>
  </div>
</div>

<header class="header">
  <div class="wrap">
    <div class="brand"><span class="mark"></span><span class="name">Harwood Institute of Training</span></div>
    <div class="actions">
      <span class="btn">Enrol Now</span>
      <span class="btn navy">Info Pack</span>
      <span class="search-btn"><svg width="18" height="18" viewBox="0 0 24 24"><circle cx="10" cy="10" r="6.5" stroke="#333" stroke-width="2.5" fill="none"/><path d="M15 15l6 6" stroke="#333" stroke-width="2.5"/></svg></span>
    </div>
  </div>
</header>

<nav class="mainnav">
  <ul>
    <li><a>Home</a></li><li><a>About Us</a></li><li><a>Recruitment</a></li><li><a>Courses</a></li><li><a>Class Schedule</a></li><li><a>Traineeships Queensland Funding</a></li><li><a>Blog</a></li><li><a>Corporate Training</a></li><li><a>Contact Us</a></li>
  </ul>
</nav>

<section class="hero" role="img" aria-label="Harbour city skyline at dusk with a steel arch bridge lit against the sunset">
  <div class="copy">
    <h1>Harwood Institute of Training</h1>
    <p>Harwood is Australia's Leading Provider of Educational, Training and Support Services for the Medical and Dental Industry</p>
    <span class="btn">Enrol Now</span>
  </div>
  <div class="dots"><i></i><i></i><i></i><i></i></div>
</section>

<section class="welcome">
  <h2 class="section-title">Welcome to our website</h2>
  <p>Harwood is Australia's Leading Provider of Educational, Training and Support Services for the Medical and Dental Industry - enabling students to be immediately skilled and 'Job Ready' for a career in Health. Harwood is a Registered Training Organisation offering specialised Medical Administration Training in over 15 locations Australia wide. Harwood have trained thousands of students the required knowledge and skills to become successful health care administrators.</p>
  <span class="btn">Read More</span>
</section>

<section class="courses">
  <div class="wrap">
    <h2 class="section-title">List of courses</h2>
    <span class="arrow l">‹</span><span class="arrow r">›</span>
    <div class="course-row">
      <div class="course">
        <div class="icon"><svg width="34" height="34" viewBox="0 0 24 24"><circle cx="12" cy="8" r="4.5" fill="#222"/><path d="M3 22c0-5 4-8 9-8s9 3 9 8z" fill="#222"/></svg></div>
        <h3>Medical Reception<br>&amp; Terminology</h3>
        <p>Lorem ipsum dolor sit amet, consect- etuer adipiscing elit, sed diam nonummy</p>
        <span class="btn">Read More</span>
      </div>
      <div class="course">
        <div class="icon"><svg width="30" height="34" viewBox="0 0 20 24"><path d="M0 0h13l7 7v17H0z" fill="#222"/><path d="M4 11h12M4 15h12M4 19h8" stroke="#fff" stroke-width="1.6"/></svg></div>
        <h3>Cert III Business<br>Administration (Medical)</h3>
        <p>Lorem ipsum dolor sit amet, consect- etuer adipiscing elit, sed diam nonummy</p>
        <span class="btn">Read More</span>
      </div>
      <div class="course">
        <div class="icon"><svg width="34" height="30" viewBox="0 0 24 20"><rect x="8" y="0" width="8" height="5" stroke="#222" stroke-width="2" fill="none"/><rect y="4" width="24" height="16" rx="2" fill="#222"/><path d="M12 8v8M8 12h8" stroke="#fff" stroke-width="2"/></svg></div>
        <h3>Medical<br>Terminology</h3>
        <p>Lorem ipsum dolor sit amet, consect- etuer adipiscing elit, sed diam nonummy</p>
        <span class="btn">Read More</span>
      </div>
      <div class="course">
        <div class="icon"><svg width="36" height="24" viewBox="0 0 30 20"><rect width="30" height="20" rx="2" stroke="#222" stroke-width="2" fill="none"/><path d="M5 6h2M10 6h2M15 6h2M20 6h2M5 10h2M10 10h2M15 10h2M20 10h2M8 15h14" stroke="#222" stroke-width="2"/></svg></div>
        <h3>Keyboard and<br>Typing</h3>
        <p>Lorem ipsum dolor sit amet, consect- etuer adipiscing elit, sed diam nonummy</p>
        <span class="btn">Read More</span>
      </div>
    </div>
  </div>
</section>

<section class="trainee">
  <h2>HR Harwood Traineeships and Jobs</h2>
  <p>Volute tacimates indoctum at duo, vix latine salutatus eu. Eius rebum reque ius ei, ioque tamquam ut mei, sui ad paulo commune delicata. An quo scaevola recu sabo scribentur. Ea duo hinc voluptaria, duo autem appareat electram cu, soleat aperiam consequuntur sed ea. Eum at elitr docendi perpetua, minim explicari ius te Vir- tute tacimates indoctum at duo, vix latine salutatus eu. Eius rebum reque ius ei, ioque tamquam ut mei, sui ad paulo commune delicata. An quo scaevola recu sabo scribentur. Ea duo hinc voluptaria, duo autem appareat electram cu, soleat aperiam consequuntur sed ea. Eum at elitr docendi perpetua.</p>
  <div class="more">View More Info &gt;&gt;</div>
</section>

<section class="blog">
  <div class="dateline"></div>
  <div class="wrap">
    <h2 class="section-title">Blogs posts</h2>
    <span class="arrow l">‹</span><span class="arrow r">›</span>
    <div class="post-row">
      <article class="post">
        <div class="date"><b>21</b> June 2016</div>
        <div class="card">
          <div class="photo" role="img" aria-label="Medical professional reviewing notes at a desk" style="background:linear-gradient(135deg,#e8eef2,#b9c8d2)"></div>
          <div class="body"><h3>Consectetuer adipiscing...</h3><p>Lorem ipsum dolor sit amet, consec etuer adipiscing elit, sed diam nonummy quis nostrud exerci tation ullam.</p></div>
          <div class="meta"><span class="rm">Read More</span><span>💬 0</span></div>
        </div>
      </article>
      <article class="post">
        <div class="date"><b>21</b> June 2016</div>
        <div class="card">
          <div class="photo" role="img" aria-label="Promotional graphic for medical receptionist training with a smiling receptionist" style="background:linear-gradient(135deg,#cfe9f2,#5fb4cf)"></div>
          <div class="body"><h3>Consectetuer adipiscing...</h3><p>Lorem ipsum dolor sit amet, consec etuer adipiscing elit, sed diam nonummy quis nostrud exerci tation ullam.</p></div>
          <div class="meta"><span class="rm">Read More</span><span>💬 0</span></div>
        </div>
      </article>
      <article class="post">
        <div class="date"><b>21</b> June 2016</div>
        <div class="card">
          <div class="photo" role="img" aria-label="Doctors in a video consultation meeting" style="background:linear-gradient(135deg,#eef1f4,#a9b7c6)"></div>
          <div class="body"><h3>Consectetuer adipiscing...</h3><p>Lorem ipsum dolor sit amet, consec etuer adipiscing elit, sed diam nonummy quis nostrud exerci tation ullam.</p></div>
          <div class="meta"><span class="rm">Read More</span><span>💬 0</span></div>
        </div>
      </article>
    </div>
  </div>
</section>

<section class="testi">
  <h2 class="section-title">Testimonials</h2>
  <span class="arrow l">‹</span><span class="arrow r">›</span>
  <div class="quote-box">
    <span class="q open">“</span><span class="q close">”</span>
    <p>I completed the course on Feb 13th. Loved it. The trainers. Priya and Jo were excellent in their delivery and knowledge. I want to say a huge thank you for the course and knowledge I came away with. I have secured a fantastic job after my first application! Such good value for money too! I would highly recommend it, I'm a mature age person so it's never too late to up -skill yourself to get what you deserve!</p>
  </div>
  <div class="author"><b>Mara Ellison</b><span>Text Writer</span></div>
</section>

<section class="split">
  <div class="why">
    <h2>Why Harwood Institute ?</h2>
    <dl>
      <dt>Quality</dt><dd>Harwood delivery quality, effective training facilitated by industry leaders...</dd>
      <dt>Experience</dt><dd>Harwood is Australia's largest and leading providers of nationally recognised training in health administration...</dd>
      <dt>Value</dt><dd>Our innovative teaching approach allows us to deliver exceptional training at affordable prices with no hidden extras.</dd>
      <dt>Industry Recognised</dt><dd>Harwood work hand in hand with industry to develop our core programme and consolidate the programme annually...</dd>
      <dt>Great Job Results</dt><dd>Harwood students get jobs! Our focus is to create job-ready students who are mentored to achieve their goals...</dd>
    </dl>
  </div>
  <div class="infopack">
    <h2>Email me an info pack</h2>
    <div class="form">
      <div class="field">Name</div>
      <div class="field">Email Address</div>
      <div class="field">Course</div>
      <div class="field">Subject</div>
      <div class="field msg">Message</div>
      <div class="send">SEND</div>
    </div>
  </div>
</section>

<section class="cta">
  <p>Lorem ipsum dolor sit amet, consect- etuer adipiscing elit,<br>sed diam nonummy nibh euismod tincidunt ut laoreet</p>
  <span class="btn">Enroll Now</span>
</section>

<footer class="footer">
  <div class="wrap">
    <div class="fcol about">
      <div class="brand"><span class="mark" style="background:#fff"></span><span class="name">Harwood Institute of Training</span></div>
      <p>Harwood Health Management started business in February 1999 primarily as a Medical and Dental Recruitment Company</p>
      <div class="fsocial"><i></i><i></i><i></i><i></i><i></i></div>
    </div>
    <div class="fcol">
      <h4>Latest Posts</h4>
      <div class="item">Ut wisi enim ad minim veniam, quis nostrud exerci tation ullam<em>21 Jun, 2016</em></div>
      <div class="item">Ut wisi enim ad minim veniam, quis nostrud exerci tation ullam<em>21 Jun, 2016</em></div>
      <div class="item">Ut wisi enim ad minim veniam, quis nostrud exerci tation ullam<em>21 Jun, 2016</em></div>
    </div>
    <div class="fcol">
      <h4>Latest Tweets</h4>
      <div class="item">Ut wisi enim ad minim veniam, quis nostrud exerci tation ullam<em>3hrs ago</em></div>
      <div class="item">Ut wisi enim ad minim veniam, quis nostrud exerci tation ullam<em>3hrs ago</em></div>
      <div class="item">Ut wisi enim ad minim veniam, quis nostrud exerci tation ullam<em>3hrs ago</em></div>
    </div>
    <div class="fcol">
      <h4>Contact Us</h4>
      <div class="contact-list">
        <div class="co">Harwood Institute</div>
        <div>14 Kestrel Lane,<br>Brindale, QLD 4000</div>
        <div><svg width="12" height="12" viewBox="0 0 24 24"><path fill="#cfd5e2" d="M6.6 10.8a15 15 0 006.6 6.6l2.2-2.2c.3-.3.7-.4 1-.2 1.1.4 2.3.6 3.6.6.6 0 1 .4 1 1V20c0 .6-.4 1-1 1A17 17 0 013 4c0-.6.4-1 1-1h3.5c.6 0 1 .4 1 1 0 1.3.2 2.5.6 3.6.1.3 0 .7-.2 1z"/></svg>1-800-555-0142</div>
        <div><svg width="12" height="10" viewBox="0 0 24 18"><rect width="24" height="18" fill="#cfd5e2"/><path d="M0 0l12 9L24 0" stroke="#1f2b47" stroke-width="2" fill="none"/></svg>info@harwoodinstitute.example</div>
      </div>
      <h4 style="margin-top:22px;margin-bottom:8px">Newsletter Sign Up</h4>
      <div class="news-in">Enter Email</div>
      <div class="news-go"><span>SIGN UP</span></div>
    </div>
  </div>
</footer>
<div class="copyright">Copyright © 2016 Company Name All Right Reserved.</div>

</body>
</html>
```